Thornvale Agribusiness Consulting needs a Website Design.

We need a website design for a new company based in UK. Thornvale offers agribusiness consulting and farm design services to farmers, smallholders and the wider agribusiness industry to assist clients in adopting more sustainable and regenerative production, processing and marketing practices.
Services are offered face-to-face and on a remote platform.
Services are offered in the UK and overseas.
We would like to see designs that reflect the natural environment, business and sustainability. Desired colours; green, blue, grey. The final design should communicate professionalism in the rural economy.
The design should be able to be customized by the client to make future changes and additions.
Target Market(s)
Farmers, smallholders, and the agricultural industry in UK and overseas.
Industry/Entity Type
Agribusiness
Number of Pages Required
4 page
Look and feel
Each slider illustrates characteristics of the customer's brand and the style your logo design should communicate.

```html
<!DOCTYPE html>
<html lang="en">
<head>
<meta charset="utf-8">
<title>Thornvale Agribusiness Consulting</title>
<link href="https://fonts.googleapis.com/css2?family=Open+Sans:wght@400;600;700&display=swap" rel="stylesheet">
<style>
:root{
  --brand-green:#159a78;
  --nav-mint:#96dfd4;
  --heading-blue:#1a7fc0;
  --caption-green:#1a9a78;
  --text-grey:#666;
  --dark:#333;
  --tweet-blue:#5bc3f0;
  --footer-dark:#343434;
  --bottom-dark:#232323;
  --footer-title:#7cc6ea;
  --subscribe:#8ec9ea;
}
*{margin:0;padding:0;box-sizing:border-box}
html,body{width:878px;height:1200px;overflow:hidden;background:#fff}
body{position:relative;font-family:"Open Sans",Arial,sans-serif;color:var(--dark)}
.abs{position:absolute}

/* header */
.site-header{left:0;top:0;width:878px;height:62px;background:var(--nav-mint)}
.brand{left:0;top:0;width:285px;height:62px;background:var(--brand-green);color:#fff;font-weight:700;font-size:25px;line-height:62px;padding-left:72px;letter-spacing:-0.3px}
.nav-item{top:0;height:62px;line-height:62px;font-size:9px;font-weight:700;color:#2f4a45;letter-spacing:0.2px}
.nav-item.active{left:285px;width:49px;background:#fff;color:var(--brand-green);text-align:center}
.search{left:662px;top:18px;width:142px;height:24px;background:#fff;font-size:8px;color:#999;line-height:24px;padding-left:11px}
.search svg{position:absolute;right:7px;top:7px}

/* hero */
.hero{left:0;top:68px;width:878px;height:364px;background:linear-gradient(to bottom,#d6dbe0 0%,#aeb8c2 55%,#8a9aa8 75%,#7fa84a 100%)}
.hero-title{right:74px;top:224px;text-align:right;font-size:21px;font-weight:700;line-height:24px;color:var(--dark);letter-spacing:0.2px}
.hero-arrow{top:238px;width:19px;height:25px;background:rgba(120,120,120,.75)}
.hero-arrow.prev{left:0}
.hero-arrow.next{right:0}

/* what we do */
.section-title{left:0;width:878px;text-align:center;font-size:19px;font-weight:700;color:var(--heading-blue);letter-spacing:0.3px}
.service-img{top:502px;width:234px;height:120px}
.service-caption{top:628px;width:234px;text-align:center;font-size:15.5px;font-weight:700;color:var(--caption-green);letter-spacing:0.3px}
.divider{left:73px;top:683px;width:731px;height:1px;background:#ddd}

/* welcome */
.welcome-text{left:120px;top:746px;width:638px;text-align:center;font-size:8.7px;line-height:16.3px;color:var(--text-grey)}
.read-more{left:402px;top:830px;width:74px;height:29px;border:1px solid var(--brand-green);color:var(--brand-green);font-size:8.5px;text-align:center;line-height:27px}

/* tweet band */
.tweet-band{left:0;top:911px;width:878px;height:119px;background:var(--tweet-blue);color:#fff}
.tweet-handle{left:190px;top:31px;font-size:10px}
.tweet-text{left:190px;top:46px;font-size:11.8px;font-weight:600}
.tweet-icons{left:190px;top:74px}

/* footer */
.footer{left:0;top:1030px;width:878px;height:100px;background:var(--footer-dark)}
.footer-title{top:20px;font-size:14px;color:var(--footer-title)}
.newsletter-input{left:73px;top:45px;width:172px;height:28px;background:#fff}
.subscribe{left:245px;top:45px;width:61px;height:28px;background:var(--subscribe);color:var(--dark);font-size:9.5px;text-align:center;line-height:28px}
.footer-rule{top:22px;width:1px;height:54px;background:#4c4c4c}
.contact-lines{left:337px;top:44px;width:244px;text-align:center;color:#eee;font-size:9.5px;line-height:16.5px}

/* bottom bar */
.bottom-bar{left:0;top:1130px;width:878px;height:70px;background:var(--bottom-dark);color:#bbb;font-size:8px}
.bottom-links{left:74px;top:18px;word-spacing:1px}
.bottom-links span{padding:0 5px;color:#888}
.copyright{left:74px;top:38px}
</style>
</head>
<body>

<header class="site-header abs">
  <div class="brand abs">Thornvale</div>
  <div class="nav-item active abs">HOME</div>
  <div class="nav-item abs" style="left:357px">ABOUT US</div>
  <div class="nav-item abs" style="left:435px">SERVICES</div>
  <div class="nav-item abs" style="left:509px">PRICING</div>
  <div class="nav-item abs" style="left:579px">CONTACT US</div>
  <div class="search abs">Search
    <svg width="10" height="10" viewBox="0 0 10 10"><circle cx="4" cy="4" r="3" fill="none" stroke="#1a7fc0" stroke-width="1.5"/><line x1="6.2" y1="6.2" x2="9" y2="9" stroke="#1a7fc0" stroke-width="1.6"/></svg>
  </div>
</header>

<section class="hero abs" role="img" aria-label="Photo of a large solitary tree in a green meadow under a cloudy sky"></section>
<h1 class="hero-title abs">CURABITUR VENENATIS<br>LACINIA ORNARE</h1>
<div class="hero-arrow prev abs"><svg width="19" height="25"><polyline points="12,6 6,12.5 12,19" fill="none" stroke="#eee" stroke-width="1"/></svg></div>
<div class="hero-arrow next abs"><svg width="19" height="25"><polyline points="7,6 13,12.5 7,19" fill="none" stroke="#eee" stroke-width="1"/></svg></div>

<h2 class="section-title abs" style="top:468px">WHAT WE DO</h2>
<div class="service-img abs" style="left:73px;background:linear-gradient(100deg,#c7d9ea,#3b5e86 60%,#1e3556)" role="img" aria-label="Photo of two consultants reviewing work at an office desk"></div>
<div class="service-img abs" style="left:322px;background:linear-gradient(90deg,#4a5560,#2b343d 60%,#1a2029)" role="img" aria-label="Photo of a businessman touching a screen of gear graphics"></div>
<div class="service-img abs" style="left:570px;background:linear-gradient(to bottom,#3b66a8,#7fa3d2)" role="img" aria-label="Photo of a businessman with a megaphone against a blue sky"></div>
<div class="service-caption abs" style="left:73px">CONSULTING</div>
<div class="service-caption abs" style="left:322px">PRODUCTION</div>
<div class="service-caption abs" style="left:570px">MARKETING</div>
<div class="divider abs"></div>

<h2 class="section-title abs" style="top:719px">WELCOME TO THORNVALE</h2>
<p class="welcome-text abs">Donec molestie nisi et tellus hendrerit vehicula. Nunc eu ligula sed quam pulvinar maximus in vitae eros. Proin porta fermentum ipsum, vel porttitor turpis venenatis luctus. Vivamus volutpat eu sapien quis tempus. Aenean feugiat viverra lorem ac sagittis. Donec sit amet lectus nec mi tempor laoreet ac nec nunc. Phasellus blandit quam a ipsum gravida dapibus. Cras sed augue tortor. Suspendisse elit ligula, iaculis dignissim justo eu, vestibulum venenatis elit. Sed egestas, nisl id cursus ultricies, turpis orci rhoncus odio, id tristique odio ex in lacus.</p>
<div class="read-more abs">READ MORE</div>

<section class="tweet-band abs">
  <svg class="abs" style="left:123px;top:32px" width="54" height="54"><circle cx="27" cy="27" r="25.5" fill="none" stroke="#fff" stroke-width="1.5"/><circle cx="27" cy="27" r="7" fill="#fff"/></svg>
  <div class="tweet-handle abs">ellamarsh@thornvale</div>
  <div class="tweet-text abs">Aenean sed quam non sapien faucibus consequat vitae sit amet orci sapien eu tellus finibus fermentum</div>
  <svg class="tweet-icons abs" width="70" height="12">
    <path d="M1 10 Q2 4 7 4 L7 1.5 L10.5 5 L7 8.5 L7 6 Q3 6 1 10Z" fill="#fff"/>
    <path d="M26 3 H29 L34 9 H37 M26 9 H29 L34 3 H37" fill="none" stroke="#fff" stroke-width="1.3"/>
    <path d="M35.5 1.5 L38 3 L35.5 4.5Z M35.5 7.5 L38 9 L35.5 10.5Z" fill="#fff"/>
    <ellipse cx="57" cy="6" rx="4.5" ry="3.5" fill="#fff"/><path d="M54 8 L53 11 L57 9Z" fill="#fff"/>
  </svg>
</section>

<footer class="footer abs">
  <div class="footer-title abs" style="left:73px">Newsletter Signup</div>
  <div class="newsletter-input abs"></div>
  <div class="subscribe abs">Subscribe</div>
  <div class="footer-rule abs" style="left:337px"></div>
  <div class="footer-title abs" style="left:337px;width:244px;text-align:center">Contact us</div>
  <div class="contact-lines abs">Call : 01632 960 418<br>E-mail : hello@thornvale.co.uk</div>
  <div class="footer-rule abs" style="left:581px"></div>
  <div class="footer-title abs" style="right:75px">Follow us on</div>
  <svg class="abs" style="left:607px;top:50px" width="200" height="22" aria-label="Social media links">
    <circle cx="11" cy="11" r="10" fill="#4a78b8"/>
    <circle cx="36" cy="11" r="10" fill="#5bc3f0"/>
    <circle cx="61" cy="11" r="10" fill="#555"/>
    <circle cx="86" cy="11" r="10" fill="#3a9e82"/>
    <circle cx="111" cy="11" r="10" fill="#159a78"/>
    <circle cx="136" cy="11" r="10" fill="#1a7fc0"/>
    <circle cx="161" cy="11" r="10" fill="#6b7f92"/>
    <circle cx="186" cy="11" r="10" fill="#6aa84f"/>
  </svg>
</footer>

<div class="bottom-bar abs">
  <div class="bottom-links abs">Home<span>|</span>About us<span>|</span>Services<span>|</span>Solutions<span>|</span>Contact us</div>
  <div class="copyright abs">Copyright &copy; 2015 &nbsp;Thornvale. &nbsp;All rights reserved.</div>
  <svg class="abs" style="left:777px;top:21px" width="26" height="26"><circle cx="13" cy="13" r="12" fill="none" stroke="#777" stroke-width="1.5"/><path d="M13 19 V8 M8.5 12 L13 7.5 L17.5 12" fill="none" stroke="#777" stroke-width="2"/></svg>
</div>

</body>
</html>
```